App Design - Career Prep Pal

We require an App Design for our new App called 'Hiring Helper'. This app is essentially an assistant to help Users prepare for job interviews, to help them get hired. <br/><br/>Users who download the App can view common Questions and Answers, save their favourite responses and also view common Interview Tips. <br/><br/>The vision for our App is for Users who are preparing for an interview (1 week before, 1 day before, even 1 hour before), are able to download, view and educate themselves on common questions and responses, and then be confident to land the job. <br/><br/>Our team has developed wireframes to help highlight what each screen should do and include. Please see attached document, which also highlights key requirements for the experience. Feel free to add/remove/edit what you see on these wireframes. Our preference is that you use Adobe XD please.<br/><br/>In terms of design guidelines, we want the experience to be simple, intuitive and 'memorable' to help Users to remember the questions/responses when they are in the interview. <br/><br/>The final design should communicate 'neat and clean professionalism'; we like the design of: jobvista net au<br/><br/>Thank you for reading! Good luck !

Target Market(s)

Professional job seekers

Font styles to use
Sans Serif

Colors

Designer to choose colors to be used in the design.

Requirements
Must have
• Please see my PixelGuild_UX file that I have uploaded
Nice to have
• Could you also please include some ideas on how we can incorporate Advertising into the app screens

```html
<!DOCTYPE html>
<html lang="en">
<head>
<meta charset="utf-8">
<title>Hiring Helper – App Screens</title>
<link href="https://fonts.googleapis.com/css2?family=Source+Sans+3:wght@400;600;700&display=swap" rel="stylesheet">
<style>
:root{
  --bg:#cfcfcf;
  --dark:#1f1f20;
  --band:#59595b;
  --paper:#f3f5fa;
  --white:#ffffff;
  --blue:#27a9d6;
  --teal:#2a93ad;
  --red:#ef5a42;
  --ink:#222326;
  --muted:#4a4b4f;
  --line:#c9ccd3;
}
*{box-sizing:border-box;margin:0;padding:0}
html,body{width:1200px;height:1066px;overflow:hidden}
body{background:var(--bg);font-family:"Source Sans 3",Arial,sans-serif;color:var(--ink);position:relative}
.label{position:absolute;font-size:9.5px;font-weight:600;letter-spacing:.2px;color:#2b2b2b}
.screen{position:absolute;width:203px;height:438px;background:var(--paper);overflow:hidden}
.screen.dark{background:var(--dark)}
.hdr{position:absolute;left:0;top:0;width:100%;height:63px;background:var(--dark)}
.hdr.tall{height:102px}
.back{position:absolute;left:10px;top:12px;color:var(--white);font-size:8.5px;font-weight:600;display:flex;align-items:center;gap:4px}
.brand{position:absolute;left:0;width:100%;text-align:center;color:var(--white);font-weight:400;display:flex;justify-content:center;align-items:center;gap:5px}
.brand .dot{width:6px;height:6px;border-radius:50%;background:var(--blue)}
.brand.sm{top:39px;font-size:13px}
.band{position:absolute;left:0;width:100%;background:var(--band);color:var(--white);font-size:8px;font-weight:700;text-align:center;letter-spacing:.3px;display:flex;flex-direction:column;justify-content:center}
.band small{font-weight:400;font-size:7px;letter-spacing:0;margin-top:2px;line-height:1.3}
.teal-band{position:absolute;left:0;top:63px;width:100%;background:var(--teal);color:var(--white);display:flex;align-items:center;padding:0 8px;gap:6px}
.teal-band p{flex:1;font-size:7.5px;line-height:1.3}
.teal-band .num{background:var(--white);color:var(--teal)}
.heading{position:absolute;left:0;width:100%;font-size:8px;font-weight:700;text-align:center}
.outline-btn{position:absolute;left:19px;width:164px;height:45px;border:2px solid var(--blue);display:flex;align-items:center;gap:10px;padding-left:12px;color:var(--blue);font-size:9.5px;font-weight:700;line-height:1.35;background:transparent}
.outline-btn svg{flex:none}
.red-btn{position:absolute;width:72px;height:25px;background:var(--red);color:var(--white);font-size:9px;font-weight:700;display:flex;align-items:center;justify-content:center;letter-spacing:.3px}
.card{position:absolute;left:10px;width:183px;background:var(--white);border:1px solid var(--line)}
.qcard{display:flex;align-items:center;gap:14px;padding:0 8px 0 7px;font-size:7.5px;line-height:1.3;color:var(--muted)}
.num{flex:none;width:15px;height:15px;border-radius:50%;background:var(--teal);color:var(--white);font-size:6.5px;font-weight:700;display:flex;align-items:center;justify-content:center}
.rcard{padding:13px 10px 0 10px;font-size:7.3px;line-height:1.3;color:var(--muted)}
.rcard h4{font-size:7.5px;font-weight:700;color:var(--ink);margin-bottom:6px}
.rcard h3{font-size:8.3px;font-weight:600;color:var(--ink);margin-bottom:6px}
.corner{position:absolute;right:8px;top:8px}
.landing-copy{position:absolute;left:36px;width:132px;top:164px;color:#bdbdbd;font-size:9.5px;line-height:1.25;text-align:center}
.frame-line{position:absolute}
.tipcard{display:flex;align-items:center;gap:11px;padding:0 8px;font-size:8px;line-height:1.35;color:var(--ink)}
.ad-art{position:absolute}
</style>
</head>
<body>

<!-- Row 1 labels -->
<div class="label" style="left:50px;top:36px">LANDING</div>
<div class="label" style="left:273px;top:36px">MENU</div>
<div class="label" style="left:493px;top:36px">VIEW QUESTIONS &amp; RESPONSES</div>
<div class="label" style="left:720px;top:36px">VIEW QUESTIONS</div>
<div class="label" style="left:948px;top:36px">VIEW QUESTION &amp; RESPONSES</div>

<!-- Landing -->
<section class="screen dark" style="left:51px;top:55px">
  <div class="brand" style="top:82px;font-size:20px"><span class="dot"></span>Hiring Helper</div>
  <div class="frame-line" style="left:19px;top:137px;width:155px;height:4px;background:var(--red)"></div>
  <div class="frame-line" style="left:19px;top:137px;width:4px;height:255px;background:var(--red)"></div>
  <div class="frame-line" style="left:180px;top:155px;width:4px;height:259px;background:var(--blue)"></div>
  <div class="frame-line" style="left:29px;top:410px;width:155px;height:4px;background:var(--blue)"></div>
  <p class="landing-copy">Lorem Ipsum is simply dummy text of the printing and typese tting industry. Lorem Ipsum has been the industry's tand ard dummy text ever since the 1500s, when an unknown print er took a galley of type and scrambled it to make a type specimen book. It has survived not only five cen turies, but also the leap into electronic type setting, remaining essentially uncha nged. It was popularised in the 1960s with the Lorem Ipsum as their default model text, and a search.</p>
</section>

<!-- Menu -->
<section class="screen" style="left:274px;top:55px">
  <div class="hdr tall"></div>
  <div class="brand" style="top:63px;font-size:17px"><span class="dot"></span>Hiring Helper</div>
  <div class="outline-btn" style="top:168px">
    <svg width="22" height="18" viewBox="0 0 22 18" fill="none" stroke="#ef5a42" stroke-width="1.6"><path d="M2 2h12v8H7l-3 3v-3H2z" fill="#ef5a42"/><path d="M9 7h11v8h-2v3l-3-3H9z"/></svg>
    <span>VIEW QUESTIONS &amp;<br>RESPONSES</span></div>
  <div class="outline-btn" style="top:231px">
    <svg width="22" height="18" viewBox="0 0 22 18" fill="none" stroke="#ef5a42" stroke-width="1.4"><rect x="1" y="4" width="20" height="13"/><path d="M7 4V1h8v3M1 9h20M9 7h4v4H9z"/></svg>
    <span>MY QUESTION<br>PORTFOLIO</span></div>
  <div class="outline-btn" style="top:296px">
    <svg width="22" height="22" viewBox="0 0 22 22" fill="none" stroke="#ef5a42" stroke-width="1.4"><circle cx="11" cy="10" r="5"/><path d="M9 15v3h4v-3M10 20h2M11 1v2M3 4l1.5 1.5M19 4l-1.5 1.5M1 10h2M19 10h2"/></svg>
    <span>INTERVIEW TIPS</span></div>
</section>

<!-- View questions & responses: categories -->
<section class="screen" style="left:497px;top:55px">
  <div class="hdr"></div>
  <div class="back"><svg width="6" height="9" viewBox="0 0 6 9"><path d="M5 1L1.5 4.5 5 8" stroke="#fff" stroke-width="1.4" fill="none"/></svg>BACK</div>
  <div class="brand sm"><span class="dot"></span>Hiring Helper</div>
  <div class="band" style="top:63px;height:25px">VIEW QUESTIONS &nbsp;&amp; RESPONSES</div>
  <div class="heading" style="top:111px;text-align:left;left:19px">SELECT YOUR QUESTIONS CATEGORY</div>
  <div class="outline-btn" style="top:131px"><svg width="22" height="22" viewBox="0 0 22 22" fill="none" stroke="#ef5a42" stroke-width="1.3"><circle cx="12" cy="10" r="8"/><path d="M6 16l-2 5M9 7h6M9 10h6M9 13h6"/></svg><span>BEHAVIORAL</span></div>
  <div class="outline-btn" style="top:194px"><svg width="24" height="20" viewBox="0 0 24 20" fill="none" stroke="#ef5a42" stroke-width="1.3"><path d="M2 7h4l10-5v16L6 13H2z M5 13l2 6h3l-1-6M19 6c2 2 2 6 0 8"/></svg><span>SITUATIONAL</span></div>
  <div class="outline-btn" style="top:259px"><svg width="22" height="24" viewBox="0 0 22 24" fill="none" stroke="#ef5a42" stroke-width="1.3"><circle cx="11" cy="9" r="7"/><path d="M8 16v4h6v-4M9 22h4M11 4v10M7 8h8"/></svg><span>MOTIVATIONAL</span></div>
  <div class="outline-btn" style="top:323px"><svg width="22" height="20" viewBox="0 0 22 20" fill="none" stroke="#ef5a42" stroke-width="1.4"><path d="M3 16v-5a8 8 0 0116 0v5"/><rect x="2" y="12" width="4" height="7" rx="1"/><rect x="16" y="12" width="4" height="7" rx="1"/></svg><span>TECHNICAL</span></div>
  <div class="red-btn" style="left:65px;top:388px">VIEW ALL</div>
</section>

<!-- View questions list -->
<section class="screen" style="left:721px;top:55px">
  <div class="hdr"></div>
  <div class="back"><svg width="6" height="9" viewBox="0 0 6 9"><path d="M5 1L1.5 4.5 5 8" stroke="#fff" stroke-width="1.4" fill="none"/></svg>BACK</div>
  <div class="brand sm"><span class="dot"></span>Hiring Helper</div>
  <div class="band" style="top:63px;height:25px">VIEW QUESTIONS &nbsp;&amp; RESPONSES</div>
  <div class="heading" style="top:105px;left:-5px">BEHAVIOURAL</div>
  <div class="card qcard" style="top:129px;height:53px"><span class="num">1.</span><p>Give me on exomple of o new ideo or initiotive you hove suggested to your manager How did you implement this idea?</p></div>
  <div class="card qcard" style="top:189px;height:53px"><span class="num">2.</span><p>Give me on example of a time when you mode a mistake or didn't deliver on expectations, what happened? Whot did you learn?</p></div>
  <div class="card qcard" style="top:250px;height:53px"><span class="num">3.</span><p>How would your colleogues describe I you in three words?</p></div>
  <div class="card qcard" style="top:311px;height:53px"><span class="num">4.</span><p>What parts of your current role frustrote you?</p></div>
  <div class="card qcard" style="top:371px;height:53px"><span class="num">5.</span><p>What steps would you toke to make on I importont decision on the job?</p></div>
</section>

<!-- View question & responses -->
<section class="screen" style="left:949px;top:55px">
  <div class="hdr"></div>
  <div class="back"><svg width="6" height="9" viewBox="0 0 6 9"><path d="M5 1L1.5 4.5 5 8" stroke="#fff" stroke-width="1.4" fill="none"/></svg>BACK</div>
  <div class="brand sm"><span class="dot"></span>Hiring Helper</div>
  <div class="teal-band" style="height:61px">
    <svg width="7" height="11" viewBox="0 0 7 11"><path d="M6 1L1.5 5.5 6 10" stroke="#fff" stroke-width="1.5" fill="none"/></svg>
    <span class="num" style="width:13px;height:13px">1.</span>
    <p>Give me on exomple of o new ideo or initiotive you hove suggested to your manager How did you implement this idea?</p>
    <svg width="7" height="11" viewBox="0 0 7 11"><path d="M1 1l4.5 4.5L1 10" stroke="#fff" stroke-width="1.5" fill="none"/></svg>
  </div>
  <div class="card rcard" style="top:136px;height:93px"><svg class="corner" width="11" height="10" viewBox="0 0 11 10"><path d="M5.5 9.5L1 5a2.6 2.6 0 014.5-3.5A2.6 2.6 0 0110 5z" fill="#ef5a42"/></svg><h4>RESPONSE 1</h4><p>Lorem ipsum dolor sit amet, consectetur adipiscing elit, sed do eiusmod tempor incididunt ut labore et dolore magna aliqua. Ut enim ad minim veniam, quis nostrud exercitation ullamco laboris,</p></div>
  <div class="card rcard" style="top:236px;height:93px"><svg class="corner" width="11" height="10" viewBox="0 0 11 10"><path d="M5.5 9.5L1 5a2.6 2.6 0 014.5-3.5A2.6 2.6 0 0110 5z" fill="#a4a6ab"/></svg><h4>RESPONSE 1</h4><p>Lorem ipsum dolor sit amet, consectetur adipiscing elit, sed do eiusmod tempor incididunt ut labore et dolore magna aliqua. Ut enim ad minim veniam, quis nostrud exercitation ullamco laboris,</p></div>
  <div class="card rcard" style="top:336px;height:93px"><svg class="corner" width="11" height="10" viewBox="0 0 11 10"><path d="M5.5 9.5L1 5a2.6 2.6 0 014.5-3.5A2.6 2.6 0 0110 5z" fill="#a4a6ab"/></svg><h4>RESPONSE 1</h4><p>Lorem ipsum dolor sit amet, consectetur adipiscing elit, sed do eiusmod tempor incididunt ut labore et dolore magna aliqua. Ut enim ad minim veniam, quis nostrud exercitation ullamco laboris,</p></div>
</section>

<!-- Row 2 labels -->
<div class="label" style="left:49px;top:540px">MY QUESTIONS PORTFOLIO</div>
<div class="label" style="left:275px;top:540px">INTERVIEW TIPS</div>
<div class="label" style="left:497px;top:540px">VIEW INTERVIEW TIPS</div>
<div class="label" style="left:720px;top:540px">VIEW INTERVIEW TIPS 1</div>
<div class="label" style="left:946px;top:540px">ADVERTISING</div>

<!-- Portfolio -->
<section class="screen" style="left:50px;top:564px">
  <div class="hdr"></div>
  <div class="back"><svg width="6" height="9" viewBox="0 0 6 9"><path d="M5 1L1.5 4.5 5 8" stroke="#fff" stroke-width="1.4" fill="none"/></svg>BACK</div>
  <div class="brand sm"><span class="dot"></span>Hiring Helper</div>
  <div class="band" style="top:63px;height:50px">MY QUESTIONS PORTFOLIO<small>These are you saved answers that you favourited.<br>We placed them here to help you prepare.</small></div>
  <div class="card rcard" style="top:126px;height:93px"><svg class="corner" width="13" height="13" viewBox="0 0 13 13"><circle cx="6.5" cy="6.5" r="6.5" fill="#ef5a42"/><path d="M4.3 4.3l4.4 4.4M8.7 4.3l-4.4 4.4" stroke="#fff" stroke-width="1.4"/></svg><h3>4. What are your greatest strengths?</h3><p>Lorem ipsum dolor sit amet, consectetur adipiscing elit, sed do eiusmod tempor incididunt ut labore et dolore magna aliqua. Ut enim ad minim veniam, quis nostrud exercitation ullamco laboris,</p></div>
  <div class="card rcard" style="top:229px;height:93px"><svg class="corner" width="13" height="13" viewBox="0 0 13 13"><circle cx="6.5" cy="6.5" r="6.5" fill="#ef5a42"/><path d="M4.3 4.3l4.4 4.4M8.7 4.3l-4.4 4.4" stroke="#fff" stroke-width="1.4"/></svg><h3>20. What do you see yourself in five?</h3><p>Lorem ipsum dolor sit amet, consectetur adipiscing elit, sed do eiusmod tempor incididunt ut labore et dolore magna aliqua. Ut enim ad minim veniam, quis nostrud exercitation ullamco laboris,</p></div>
  <div class="card rcard" style="top:332px;height:93px"><svg class="corner" width="13" height="13" viewBox="0 0 13 13"><circle cx="6.5" cy="6.5" r="6.5" fill="#ef5a42"/><path d="M4.3 4.3l4.4 4.4M8.7 4.3l-4.4 4.4" stroke="#fff" stroke-width="1.4"/></svg><h3>36. Why should we hire you?</h3><p>Lorem ipsum dolor sit amet, consectetur adipiscing elit, sed do eiusmod tempor incididunt ut labore et dolore magna aliqua. Ut enim ad minim veniam, quis nostrud exercitation ullamco laboris,</p></div>
</section>

<!-- Interview tips categories -->
<section class="screen" style="left:275px;top:564px">
  <div class="hdr tall"></div>
  <div class="brand" style="top:63px;font-size:17px;opacity:.45"><span class="dot"></span>Hiring Helper</div>
  <div class="band" style="top:102px;height:25px">INTERVIEW TIPS</div>
  <div class="heading" style="top:155px;text-align:left;left:19px">SELECT YOUR QUESTIONS CATEGORY</div>
  <div class="outline-btn" style="top:181px"><svg width="22" height="22" viewBox="0 0 22 22" fill="none" stroke="#ef5a42" stroke-width="1.4"><circle cx="11" cy="10" r="5"/><path d="M9 15v3h4v-3M10 20h2M11 1v2M3 4l1.5 1.5M19 4l-1.5 1.5M1 10h2M19 10h2"/></svg><span>TIPS FOR BEFORE<br>THE INTERVIEW</span></div>
  <div class="outline-btn" style="top:245px"><svg width="22" height="22" viewBox="0 0 22 22" fill="none" stroke="#ef5a42" stroke-width="1.4"><circle cx="11" cy="10" r="5"/><path d="M9 15v3h4v-3M10 20h2M11 1v2M3 4l1.5 1.5M19 4l-1.5 1.5M1 10h2M19 10h2"/></svg><span>TIPS FOR DURING<br>THE INTERVIEW</span></div>
  <div class="outline-btn" style="top:310px"><svg width="22" height="22" viewBox="0 0 22 22" fill="none" stroke="#ef5a42" stroke-width="1.4"><circle cx="11" cy="10" r="5"/><path d="M9 15v3h4v-3M10 20h2M11 1v2M3 4l1.5 1.5M19 4l-1.5 1.5M1 10h2M19 10h2"/></svg><span>TIPS FOR AFTER<br>THE INTERVIEW</span></div>
  <div class="red-btn" style="left:60px;top:379px">VIEW ALL</div>
</section>

<!-- View interview tips list -->
<section class="screen" style="left:497px;top:564px">
  <div class="hdr"></div>
  <div class="back"><svg width="6" height="9" viewBox="0 0 6 9"><path d="M5 1L1.5 4.5 5 8" stroke="#fff" stroke-width="1.4" fill="none"/></svg>BACK</div>
  <div class="brand sm"><span class="dot"></span>Hiring Helper</div>
  <div class="band" style="top:63px;height:25px">INTERVIEW TIPS</div>
  <div class="card tipcard" style="top:100px;height:40px"><span class="num">1.</span><p>Start by researching the company and your interviewers.</p></div>
  <div class="card tipcard" style="top:146px;height:40px"><span class="num">2.</span><p>Practive your anserrs to common interview questions.</p></div>
  <div class="card tipcard" style="top:192px;height:40px"><span class="num">3.</span><p>Re-read the job description</p></div>
  <div class="card tipcard" style="top:238px;height:40px"><span class="num">4.</span><p>Use the STAR methods in answering questions</p></div>
  <div class="card tipcard" style="top:284px;height:40px"><span class="num">5.</span><p>Recruit a friend to practive answering questions.</p></div>
  <div class="card tipcard" style="top:331px;height:40px"><span class="num">6.</span><p>Prepare a list of references</p></div>
  <div class="card tipcard" style="top:378px;height:40px"><span class="num">7.</span><p>Be prepared with examples of your work</p></div>
</section>

<!-- View interview tip detail -->
<section class="screen" style="left:721px;top:564px">
  <div class="hdr"></div>
  <div class="back"><svg width="6" height="9" viewBox="0 0 6 9"><path d="M5 1L1.5 4.5 5 8" stroke="#fff" stroke-width="1.4" fill="none"/></svg>BACK</div>
  <div class="brand sm"><span class="dot"></span>Hiring Helper</div>
  <div class="teal-band" style="height:43px">
    <svg width="7" height="11" viewBox="0 0 7 11"><path d="M6 1L1.5 5.5 6 10" stroke="#fff" stroke-width="1.5" fill="none"/></svg>
    <span class="num" style="width:13px;height:13px">8.</span>
    <p style="font-size:8.5px">Be prepared with examples of your work</p>
    <svg width="7" height="11" viewBox="0 0 7 11"><path d="M1 1l4.5 4.5L1 10" stroke="#fff" stroke-width="1.5" fill="none"/></svg>
  </div>
  <div class="card" style="top:119px;height:176px;padding:16px 14px;font-size:10px;line-height:1.42;color:var(--ink)">During the interview, you will likely be asked about specific work you've completed in relation to the position. After reviewing the job description, think of work you've done in post jobs, clubs or volunteer positions that show you have experience and success doing the work they require.</div>
</section>

<!-- Advertising -->
<section class="screen" style="left:949px;top:564px">
  <div class="hdr"></div>
  <div class="back"><svg width="6" height="9" viewBox="0 0 6 9"><path d="M5 1L1.5 4.5 5 8" stroke="#fff" stroke-width="1.4" fill="none"/></svg>BACK</div>
  <div class="brand sm"><span class="dot"></span>Hiring Helper</div>
  <div class="ad-art" role="img" aria-label="Colourful abstract wave shapes in teal, pink and yellow" style="left:0;top:63px;width:80px;height:78px;background:linear-gradient(135deg,#f6c744,#26b8c8 50%,#ef2f74);border-bottom-right-radius:60px"></div>
  <div class="ad-art" role="img" aria-label="Colourful abstract wave shapes in pink, teal and yellow" style="right:0;bottom:0;width:85px;height:70px;background:linear-gradient(135deg,#ef2f74,#26b8c8 55%,#f6c744);border-top-left-radius:70px"></div>
  <div class="heading" style="top:183px;color:var(--teal);font-size:13.5px;line-height:1.3">LOREM IPSUM<br>DOLOR SIT AMET</div>
  <p style="position:absolute;left:18px;width:167px;top:232px;font-size:7.5px;line-height:1.3;text-align:center;color:var(--ink)">Lorem ipsum dolor sit amet, consectetur adipiscing elit, sed do eiusmod tempor incididunt ut labore et dolore magna aliqua. Ut enim ad minim veniam, quis nostrud exercitation ullamco laboris,</p>
  <div class="red-btn" style="left:65px;top:291px">READ MORE</div>
</section>

</body>
</html>
```